Thornbury Spa

We are a large Miami Beach spa and salon. I am still building our website but you can use it as a resource to gain a better understanding of who we are ....www.velloraspa-studio.com.

We offer a comprehensive list of services in hair, nails, massage, skin care, tanning, spray tanning and waxing and we offer high quality products for skin care, tanning and hair. We are open 7 days.

We would like to see a clean and simple menu that looks a lot like the one from "The Spa at Larkwood." In particular, we have a copy of a menu from their West Hollywood, CA location that is just beautiful. In the uploaded content you will see a sampling of that menu. We would like to see greys, blacks, silvers, whites and warm colors like reds and oranges. We specifically attempt to remain gender neutral so that we don't attract only girls (with pink colors and flowers etc). The final design should convey a simple, clean, friendly environment and the final product should be sized such that it is 1.) portable and 2.) inexpensive to print. We will be running thousands of these at a time so cost of printing is a consideration.

The booklet consists of two parts: one part is the standard menu with descriptions of services and products and photos etc (think of this as the sales piece that convinces a potential customer to visit) and will be stapled together like you would expect a small menu to be and should resemble the Larkwood menu. The prices should not be included in this part of the booklet that will be printed and stapled. The other part is a single insert and is removable and replaceable. I want this removable insert placed in the last page of the book in a folder pocket or something else that you can think of so that when it's time to change prices here that I am not throwing away all of the booklets....I am only replacing the inserts at the end of the menu booklet. Please design this single page insert so that should a customer remove it from the booklet and keep it, that it stands alone with our name, logo, website and phone number. This page can and probably will have to be 2 sided.

At the back of the booklet, I also want the polices to be printed in one page (think fine print in any sort of business dealing.)

With regard to the look and feel slider of economical v upmarket...we definitely want to convey we deliver upmarket services at reasonable prices. Think, world class services and products at reasonable, everyday prices.

With regard to the uploaded files:
I uploaded both EPS and TIF formats. The colors in those files are not the palette we want at all. The colors we want use for the circular logo must match the standard colors as depicted in the uploaded file "Thornburytanrooms"

Target Market(s)

The target market is the average 20-35 year old in Miami Beach that cares about their appearance. The range of clientele is quite diverse.

Industry/Entity Type

Environment

Requirements
Must have
• It must have elegant and simple photographs that relate to the services being offered. We are selling a service set and an environment...so this menu should be reflect that goal. The logo should be repeated often throughout the book but in subtle ways.

Stock photos are fine as long as they don't seem obviously stock.

Should not have
• Nothing buddha like. Nothing themed. It should be all inclusive and not seek to identify with any particular group or gender.

Nothing that fits the stereotype of "Miami Beach." We want to represent ourselves in the same category as the best spas in the world because we moving everything we do in that direction. Think class!

```html
<!DOCTYPE html>
<html lang="en">
<head>
<meta charset="utf-8">
<title>Thornbury Spa — Menu Booklet Spreads</title>
<link href="https://fonts.googleapis.com/css2?family=Didact+Gothic&display=swap" rel="stylesheet">
<style>
  :root {
    --canvas: #e8e8e8;
    --panel-dark: #262525;
    --panel-mid: #3d3c3c;
    --bar-light: #a3a3a3;
    --bar-dark: rgba(110,110,110,.55);
    --text-body: #b9b9b9;
    --text-head: #d8d8d8;
    --title: #ffffff;
    --folio: #a9a9a9;
    --ghost-word: rgba(255,255,255,.32);
    --rust: #b9552f;
    --orange: #d27a2b;
    --mauve: #8b5d86;
    --teal: #23878b;
    --stone: #6f6964;
    --silver: #a7a5a5;
  }
  html, body { margin: 0; padding: 0; overflow: hidden; }
  body { width: 1200px; height: 900px; background: var(--canvas); font-family: "Didact Gothic", "Century Gothic", sans-serif; }
  .canvas { position: relative; width: 1200px; height: 900px; }

  .folio { position: absolute; font-size: 15px; color: var(--folio); letter-spacing: 1px; }

  .spread {
    --et: 215px; --eb: 195px; --brand-x: 228px; --cols-x: 315px;
    position: absolute; width: 495px; height: 176px; overflow: hidden;
    background: linear-gradient(90deg, var(--panel-dark) 0%, var(--panel-mid) 55%, var(--panel-dark) 100%);
    box-shadow: 0 1px 3px rgba(0,0,0,.35);
  }
  .photo {
    position: absolute; left: 0; top: 0; bottom: 0; width: 260px;
    background: var(--photo);
    clip-path: polygon(0 0, var(--et) 0, var(--eb) 100%, 0 100%);
  }
  .band {
    position: absolute; left: 0; top: 0; bottom: 0; width: 300px;
    background: var(--accent);
    clip-path: polygon(var(--et) 0, calc(var(--et) + 16px) 0, calc(var(--eb) + 16px) 100%, var(--eb) 100%);
  }
  .title-bar {
    position: absolute; top: 10px; right: 0; left: calc(var(--et) + 16px); height: 22px;
    background: linear-gradient(90deg, var(--bar-dark), #8a8a8a 45%, var(--bar-light));
  }
  .title-bar h2 {
    margin: 0; position: absolute; right: 8px; top: 0; line-height: 22px;
    font-size: 20px; font-weight: 400; color: var(--title); letter-spacing: .5px; white-space: nowrap;
  }
  .ghost-word {
    position: absolute; margin: 0; color: var(--ghost-word); font-weight: 400;
    line-height: 1; white-space: nowrap; letter-spacing: 1px;
  }
  .ghost-word--top { top: 6px; left: 6px; font-size: 44px; }
  .ghost-word--bottom { bottom: 6px; left: 6px; font-size: 30px; }
  .ghost-word--vertical { left: 4px; bottom: 6px; font-size: 36px; transform-origin: left bottom; transform: rotate(-90deg) translate(0, 100%); }

  .brand {
    position: absolute; left: var(--brand-x); top: 58px; width: 60px; text-align: center;
    color: var(--text-head);
  }
  .brand-dot { display: block; width: 7px; height: 7px; margin: 0 auto 3px; border-radius: 50%; background: var(--text-head); opacity: .8; }
  .brand-name { font-size: 4.6px; letter-spacing: .8px; text-transform: uppercase; }

  .columns {
    position: absolute; left: var(--cols-x); right: 12px; top: 42px;
    display: grid; grid-template-columns: 1fr 1fr; column-gap: 12px;
  }
  .columns--single { grid-template-columns: 1fr; right: 80px; }
  .service { margin-bottom: 5px; }
  .service h3 {
    margin: 0 0 2px; padding: 1px 0; font-size: 4.4px; font-weight: 400;
    letter-spacing: .6px; text-transform: uppercase; text-align: center;
    color: var(--text-head); background: rgba(255,255,255,.13);
  }
  .service p { margin: 0; font-size: 4.2px; line-height: 1.5; color: var(--text-body); }
  .service ul { list-style: none; margin: 0; padding: 0; text-align: center; }
  .service li { font-size: 4.2px; line-height: 1.55; color: var(--text-body); }

  /* reversed spread: text left, photo right */
  .spread--reverse .photo {
    left: 316px; width: 179px; clip-path: polygon(26px 0, 100% 0, 100% 100%, 0 100%);
  }
  .spread--reverse .band {
    left: 300px; width: 42px; clip-path: polygon(26px 0, 42px 0, 16px 100%, 0 100%);
  }
  .spread--reverse .columns { left: 14px; right: 225px; top: 18px; }
  .spread--reverse .brand { left: 258px; }
  .spread--reverse .ghost-word--vertical-right {
    right: 4px; top: 6px; font-size: 36px; transform-origin: right top; transform: rotate(90deg) translate(100%, 0);
  }

  /* themes */
  .spread--hair { --accent: var(--rust); --photo: linear-gradient(120deg, #5a2416 0%, #9a4a2a 35%, #d4a07f 60%, #3a1f18 100%); }
  .spread--nails { --et: 148px; --eb: 172px; --brand-x: 178px; --cols-x: 255px; --accent: var(--mauve); --photo: linear-gradient(160deg, #c9a2a6 0%, #efe6e2 45%, #b28a80 100%); }
  .spread--massage { --et: 160px; --eb: 185px; --brand-x: 192px; --cols-x: 262px; --accent: var(--rust); --photo: linear-gradient(150deg, #5a2a18 0%, #c27a45 45%, #e9cf9c 70%, #7a3a22 100%); }
  .spread--massage-more { --accent: var(--rust); --photo: linear-gradient(200deg, #3a2016 0%, #a86a44 40%, #e6dccb 70%, #6d3a26 100%); }
  .spread--skin { --et: 150px; --eb: 142px; --brand-x: 170px; --cols-x: 262px; --accent: var(--stone); --photo: linear-gradient(135deg, #4a4744 0%, #bfb2a6 40%, #e8ddd2 60%, #5b5551 100%); }
  .spread--tanning { --et: 145px; --eb: 128px; --brand-x: 170px; --cols-x: 262px; --accent: var(--teal); --photo: linear-gradient(150deg, #2a2120 0%, #6c5a52 35%, #d9dde0 55%, #2c2626 100%); }
  .spread--waxing { --et: 200px; --eb: 185px; --brand-x: 222px; --cols-x: 290px; --accent: var(--silver); --photo: linear-gradient(160deg, #c7c5c6 0%, #e9e8e8 40%, #8f7a72 65%, #d6d4d4 100%); }
  .spread--policies { --et: 145px; --eb: 128px; --brand-x: 168px; --cols-x: 240px; --accent: var(--orange); --photo: linear-gradient(160deg, #6a5a92 0%, #c38c9e 35%, #e89a4a 60%, #4a2c1c 100%); }
  .spread--policies .columns { top: 38px; }
  .spread--policies .service { margin-bottom: 3px; }
</style>
</head>
<body>
<main class="canvas">

  <!-- Hair 1–2 -->
  <span class="folio" style="left:20px;top:135px">1.</span>
  <span class="folio" style="left:566px;top:135px">2.</span>
  <section class="spread spread--hair" style="left:55px;top:52px">
    <div class="photo" role="img" aria-label="Portrait photo of a model with glossy auburn styled hair"></div>
    <div class="band"></div>
    <p class="ghost-word ghost-word--top">HAIR</p>
    <div class="title-bar"><h2>HAIR MENU</h2></div>
    <div class="brand"><span class="brand-dot"></span><span class="brand-name">Thornbury Spa</span></div>
    <div class="columns">
      <div>
        <div class="service"><h3>Styling</h3><ul><li>men's haircut and finish</li><li>women's cut and blowout</li><li>children's haircut</li></ul></div>
        <div class="service"><h3>Styling</h3><ul><li>wet head blowout</li><li>shampoo and blowout</li><li>updo or styling</li><li>wedding hair trial</li><li>bridal styling</li></ul></div>
        <div class="service"><h3>Treatments</h3><ul><li>deep masque and nourishing treatment</li><li>keratin smoothing treatment</li><li>scalp therapy ritual</li></ul></div>
      </div>
      <div>
        <div class="service"><h3>Extensions</h3><ul><li>tape-in hair extensions</li><li>extension removal</li></ul></div>
        <div class="service"><h3>Coloring</h3><ul><li>single process</li><li>partial highlights</li><li>full highlights</li><li>double process</li></ul></div>
      </div>
    </div>
  </section>

  <!-- Nails 3–4 -->
  <span class="folio" style="left:20px;top:342px">3.</span>
  <span class="folio" style="left:566px;top:342px">4.</span>
  <section class="spread spread--nails" style="left:55px;top:262px">
    <div class="photo" role="img" aria-label="Photo of a bright nail salon with white pedicure chairs"></div>
    <div class="band"></div>
    <p class="ghost-word ghost-word--top">NAILS</p>
    <div class="title-bar"><h2>NAILS MENU</h2></div>
    <div class="brand"><span class="brand-dot"></span><span class="brand-name">Thornbury Spa</span></div>
    <div class="columns">
      <div>
        <div class="service"><h3>The Classic</h3><p>Our signature treatment begins with a warm soak, followed by careful shaping, cuticle care and a soothing massage to finish.</p></div>
        <div class="service"><h3>Deluxe</h3><p>Designed to ease tension and restore balance, this service blends gentle technique with premium products for a calm, refreshed feeling.</p></div>
        <div class="service"><h3>Natural Nail Overlays</h3><p>Your therapist tailors every step to your needs, so you leave looking polished and feeling deeply cared for by our team.</p></div>
      </div>
      <div>
        <div class="service"><h3>The Express</h3><p>Our signature treatment begins with a warm soak, followed by careful shaping, cuticle care and a soothing massage to finish.</p></div>
        <div class="service"><h3>The Ultimate</h3><p>Designed to ease tension and restore balance, this service blends gentle technique with premium products for a calm, refreshed feeling.</p></div>
        <div class="service"><h3>Nail Bar Polishing</h3><p>Your therapist tailors every step to your needs, so you leave looking polished and feeling deeply cared for by our team.</p></div>
      </div>
    </div>
  </section>

  <!-- Massage 5–6 -->
  <span class="folio" style="left:20px;top:540px">5.</span>
  <span class="folio" style="left:566px;top:540px">6.</span>
  <section class="spread spread--massage" style="left:55px;top:460px">
    <div class="photo" role="img" aria-label="Photo of a candlelit massage room with a draped treatment table and petals"></div>
    <div class="band"></div>
    <p class="ghost-word ghost-word--vertical">MASSAGE</p>
    <div class="title-bar"><h2>MASSAGE MENU</h2></div>
    <div class="brand"><span class="brand-dot"></span><span class="brand-name">Thornbury Spa</span></div>
    <div class="columns">
      <div>
        <div class="service"><h3>Swedish Massage</h3><p>Our signature treatment begins with a warm soak, followed by careful shaping, cuticle care and a soothing massage to finish.</p></div>
        <div class="service"><h3>Hot Stone Therapy</h3><p>Designed to ease tension and restore balance, this service blends gentle technique with premium products for a calm, refreshed feeling.</p></div>
        <div class="service"><h3>Prenatal Massage</h3><p>Your therapist tailors every step to your needs, so you leave looking polished and feeling deeply cared for by our team.</p></div>
      </div>
      <div>
        <div class="service"><h3>Sports – Specific Massage</h3><p>Our signature treatment begins with a warm soak, followed by careful shaping, cuticle care and a soothing massage to finish.</p></div>
        <div class="service"><h3>Thai Massage</h3><p>Designed to ease tension and restore balance, this service blends gentle technique with premium products for a calm, refreshed feeling.</p></div>
      </div>
    </div>
  </section>

  <!-- Massage 7–8 -->
  <span class="folio" style="left:20px;top:752px">7.</span>
  <span class="folio" style="left:566px;top:752px">8.</span>
  <section class="spread spread--reverse spread--massage-more" style="left:55px;top:672px">
    <div class="photo" role="img" aria-label="Photo of a warm massage suite with two treatment tables"></div>
    <div class="band"></div>
    <p class="ghost-word ghost-word--vertical-right">MASSAGE</p>
    <div class="brand"><span class="brand-dot"></span><span class="brand-name">Thornbury Spa</span></div>
    <div class="columns">
      <div>
        <div class="service"><h3>Shiatsu</h3><p>Our signature treatment begins with a warm soak, followed by careful shaping, cuticle care and a soothing massage to finish.</p></div>
        <div class="service"><h3>Aromatherapy</h3><p>Designed to ease tension and restore balance, this service blends gentle technique with premium products for a calm, refreshed feeling.</p></div>
      </div>
      <div>
        <div class="service"><h3>Reflexology</h3><p>Your therapist tailors every step to your needs, so you leave looking polished and feeling deeply cared for by our team.</p></div>
        <div class="service"><h3>Deep Tissue Massage</h3><p>Our signature treatment begins with a warm soak, followed by careful shaping, cuticle care and a soothing massage to finish.</p></div>
      </div>
    </div>
  </section>

  <!-- Skin care 9–10 -->
  <span class="folio" style="left:618px;top:108px">9.</span>
  <span class="folio" style="left:1158px;top:108px">10.</span>
  <section class="spread spread--skin" style="left:650px;top:33px">
    <div class="photo" role="img" aria-label="Photo of a model with clear glowing skin resting her head on her hand"></div>
    <div class="band"></div>
    <p class="ghost-word ghost-word--bottom">SKIN CARE</p>
    <div class="title-bar"><h2>SKIN CARE</h2></div>
    <div class="brand"><span class="brand-dot"></span><span class="brand-name">Thornbury Spa</span></div>
    <div class="columns">
      <div>
        <div class="service"><h3>Chemical Peel</h3><p>Our signature treatment begins with a warm soak, followed by careful shaping, cuticle care and a soothing massage to finish.</p></div>
        <div class="service"><h3>Clinical Facial</h3><p>Designed to ease tension and restore balance, this service blends gentle technique with premium products for a calm, refreshed feeling.</p></div>
      </div>
      <div>
        <div class="service"><h3>Microdermabrasion</h3><p>Your therapist tailors every step to your needs, so you leave looking polished and feeling deeply cared for by our team.</p></div>
        <div class="service"><h3>Organic Facial</h3><p>Our signature treatment begins with a warm soak, followed by careful shaping, cuticle care and a soothing massage to finish.</p></div>
      </div>
    </div>
  </section>

  <!-- Tanning 11–12 -->
  <span class="folio" style="left:612px;top:330px">11.</span>
  <span class="folio" style="left:1158px;top:330px">12.</span>
  <section class="spread spread--tanning" style="left:650px;top:252px">
    <div class="photo" role="img" aria-label="Photo of a modern tanning bed in a dim studio"></div>
    <div class="band"></div>
    <p class="ghost-word ghost-word--vertical">TANNING</p>
    <div class="title-bar"><h2>SKIN CARE</h2></div>
    <div class="brand"><span class="brand-dot"></span><span class="brand-name">Thornbury Spa</span></div>
    <div class="columns">
      <div>
        <div class="service"><h3>UV Tanning</h3><p>Our signature treatment begins with a warm soak, followed by careful shaping, cuticle care and a soothing massage to finish.</p></div>
        <div class="service"><h3>Custom Airbrush Tanning</h3><p>Designed to ease tension and restore balance, this service blends gentle technique with premium products for a calm, refreshed feeling.</p></div>
      </div>
      <div>
        <div class="service"><h3>UV Series</h3><p>Your therapist tailors every step to your needs, so you leave looking polished and feeling deeply cared for by our team.</p></div>
      </div>
    </div>
  </section>

  <!-- Threading & waxing 13–14 -->
  <span class="folio" style="left:612px;top:548px">13.</span>
  <span class="folio" style="left:1158px;top:548px">14.</span>
  <section class="spread spread--waxing" style="left:650px;top:470px">
    <div class="photo" role="img" aria-label="Photo of a model in a swimsuit seated on a white block"></div>
    <div class="band"></div>
    <p class="ghost-word ghost-word--bottom">THREADING<br>&amp; WAXING</p>
    <div class="title-bar"><h2>THREADING &amp; WAXING</h2></div>
    <div class="brand"><span class="brand-dot"></span><span class="brand-name">Thornbury Spa</span></div>
    <div class="columns columns--single">
      <div>
        <div class="service"><h3>Threading</h3><p>Our signature treatment begins with a warm soak, followed by careful shaping, cuticle care and a soothing massage to finish.</p></div>
        <div class="service"><h3>Waxing</h3><p>Designed to ease tension and restore balance, this service blends gentle technique with premium products for a calm, refreshed feeling.</p></div>
      </div>
    </div>
  </section>

  <!-- Policies 15–16 -->
  <span class="folio" style="left:612px;top:768px">15.</span>
  <span class="folio" style="left:1158px;top:768px">16.</span>
  <section class="spread spread--policies" style="left:650px;top:688px">
    <div class="photo" role="img" aria-label="Photo of a softly lit spa lounge with a low table and vase"></div>
    <div class="band"></div>
    <p class="ghost-word ghost-word--vertical">POLICES</p>
    <div class="title-bar"><h2>POLICES</h2></div>
    <div class="brand"><span class="brand-dot"></span><span class="brand-name">Thornbury Spa</span></div>
    <div class="columns">
      <div>
        <div class="service"><h3>Etiquette &amp; Expectations</h3><p>Our signature treatment begins with a warm soak, followed by careful shaping, cuticle care and a soothing massage to finish.</p></div>
        <div class="service"><h3>Late Arrivals &amp; Cancellations</h3><p>Designed to ease tension and restore balance, this service blends gentle technique with premium products for a calm, refreshed feeling.</p></div>
        <div class="service"><h3>Gift Cards</h3><p>Your therapist tailors every step to your needs, so you leave looking polished and feeling deeply cared for by our team.</p></div>
        <div class="service"><h3>Spa Attire</h3><p>Our signature treatment begins with a warm soak, followed by careful shaping, cuticle care and a soothing massage to finish.</p></div>
      </div>
      <div>
        <div class="service"><h3>Service Charges &amp; Gratuity</h3><p>Designed to ease tension and restore balance, this service blends gentle technique with premium products for a calm, refreshed feeling.</p></div>
        <div class="service"><h3>Valuables</h3><p>Your therapist tailors every step to your needs, so you leave looking polished and feeling deeply cared for by our team.</p></div>
        <div class="service"><h3>Refunds</h3><p>Our signature treatment begins with a warm soak, followed by careful shaping, cuticle care and a soothing massage to finish.</p></div>
        <div class="service"><h3>Age Policy</h3><p>Designed to ease tension and restore balance, this service blends gentle technique with premium products for a calm, refreshed feeling.</p></div>
      </div>
    </div>
  </section>

</main>
</body>
</html>
```